Tellmora Corporate Stationery

Look for design of all new corporate stationery for an existing insurance broking business that is going through a redesign and move from older partners to younger family members. New Logo is attached. Company is Brisbane based.
Colours in the Logo is Hex #43bed8 and website features a lot of hex #17b8d8. Website front page "A plan to protect you" - headline. "Professional and Individual advice to protect your greatest assets" - tagline.

Stationery required: Business Cards, Letter head, Thank-you cards, Birthday cards, Presentation folders, With Compliment slips and a powerpoint template. We also would like to send a card to all customers with the something along of the lines of "something new".

Target Market(s)

Customers of Insurance business looking at superannuation, life and income protection insurance, investment advice and wills

Industry/Entity Type

Insurance Broker

Font styles to use
Other font styles liked:
• same as logo

Requirements
Must have
• The above designs for new stationery for the new business including:
• Business Cards, Letter head, Thank-you cards, Birthday cards, Presentation folders, With Compliment slips and a powerpoint template. We also would like to send a card to all customers with the something along of the lines of "something new".
Nice to have
• It is a new look - long time family business being passed to next generation - big focus on advice for YOU, individual advice etc..

```html
<!DOCTYPE html>
<html lang="en">
<head>
<meta charset="utf-8">
<title>Tellmora Financial Group – Presentation Slide Sets</title>
<link rel="stylesheet" href="https://fonts.googleapis.com/css2?family=Open+Sans:wght@400;600;700&display=swap">
<style>
:root{
  --stage:#000;
  --brand:#3fbdd8;
  --brand-bright:#17b8d8;
  --teal-deep:#1d6f80;
  --teal-band:#1f7a8c;
  --ice:#e4f5f9;
  --ice-mid:#c9ecf4;
  --grey:#6d6e71;
  --grey-mid:#8a8b8d;
  --text:#555;
  --white:#fff;
}
*{margin:0;padding:0;box-sizing:border-box}
html,body{width:1200px;height:1200px;overflow:hidden;background:var(--stage);font-family:"Open Sans",Arial,sans-serif}
.canvas{position:relative;width:1200px;height:1200px}
.set-label{position:absolute;color:var(--white);font-size:22px;font-weight:400;transform:translateX(-50%)}
.slide{position:absolute;overflow:hidden}
.slide > *{position:absolute}
.brand-name{color:var(--brand);font-weight:700;letter-spacing:2px;line-height:1;text-align:center}
.brand-name small{display:block;color:var(--grey);font-weight:700;letter-spacing:1px}
.lorem{color:var(--text);line-height:1.85}
.contact{line-height:1.7}
.contact span{display:flex;align-items:center;gap:4px;white-space:nowrap}
.contact i{display:inline-block;width:7px;height:7px;border-radius:2px;background:currentColor;opacity:.85}

/* set 1 */
.s1{left:41px;top:178px;width:521px;height:388px;background:linear-gradient(#fff 0%,#fff 45%,#d6eff6 70%)}
.s1 .scene-art{left:18px;top:22px;width:240px;height:312px;border-radius:4px;background:linear-gradient(180deg,#e3f3f8 0%,#c7e6f0 45%,#b9d9e8 62%,#e8d9a2 82%,#dcbf66 100%)}
.s1 .welcome{left:265px;width:240px;text-align:center;top:80px;font-size:46px;font-weight:700;color:var(--brand);letter-spacing:1px}
.s1 .brand-name{left:285px;top:150px;width:190px;font-size:20px}
.s1 .brand-name small{font-size:10.5px;margin-top:5px}
.s1 .headline{left:268px;top:298px;font-size:18.5px;font-weight:700;color:var(--white)}
.s1 .tagline{left:268px;top:321px;font-size:7.5px;color:var(--white)}
.s1 .contact{left:20px;top:326px;font-size:8px;color:var(--white)}
.s1 .licence{right:14px;top:354px;font-size:9px;color:var(--white);text-align:right;line-height:1.65;letter-spacing:.3px}

/* set 2 */
.s2{left:611px;top:177px;width:517px;height:387px;background:linear-gradient(#e8f6f9 0%,#f3fafc 70%,#fff 72%)}
.s2 .topband{left:0;top:0;width:517px;height:77px;background:linear-gradient(#fff,#d3eef5)}
.s2 .figure-art{left:361px;top:13px;width:156px;height:264px;background:linear-gradient(#cdeef4,#b9e4ee)}
.s2 .headline{left:18px;top:20px;font-size:22.5px;font-weight:700;color:var(--teal-deep)}
.s2 .tagline{right:164px;top:48px;font-size:8px;color:var(--grey-mid)}
.s2 .lorem{left:12px;top:83px;width:340px;font-size:6.8px;line-height:1.9}
.s2 .welcome{left:230px;top:230px;font-size:28px;color:var(--brand)}
.s2 .brand-name{left:170px;top:298px;width:250px;font-size:28px}
.s2 .brand-name small{font-size:16px;margin-top:3px}
.s2 .contact{left:8px;top:337px;font-size:6.5px;color:var(--text);line-height:1.65}
.s2 .licence{right:12px;top:366px;font-size:9px;color:var(--grey);letter-spacing:.3px}

/* set 3 */
.s3{left:40px;top:728px;width:522px;height:390px;background:linear-gradient(170deg,#fff 0%,#e6f6fa 40%,#8fd3e4 100%)}
.s3 .headline{left:28px;top:20px;font-size:29px;font-weight:700;color:var(--teal-deep);letter-spacing:.5px}
.s3 .tagline{left:60px;top:55px;font-size:12px;color:#2a8ba3}
.s3 .lorem.a{left:22px;top:92px;width:345px;font-size:7px}
.s3 .lorem.b{left:22px;top:137px;width:180px;font-size:7px}
.s3 .brand-name{left:240px;top:288px;width:135px;font-size:16px}
.s3 .brand-name small{font-size:9px;margin-top:2px}
.s3 .contact{right:25px;top:305px;font-size:8px;color:var(--teal-deep);text-align:right}
.s3 .contact span{justify-content:flex-end}
.s3 .band{left:8px;top:362px;width:514px;height:21px;background:var(--teal-band)}
.s3 .licence{right:25px;top:366px;font-size:9px;font-weight:700;color:var(--white);letter-spacing:.5px}

/* set 4 */
.s4{left:610px;top:728px;width:518px;height:388px;background:var(--white)}
.s4 .headline{left:26px;top:34px;font-size:30px;font-weight:700;color:var(--teal-deep);line-height:1.3;letter-spacing:.5px}
.s4 .headline span{display:block;padding-left:36px}
.s4 .tagline{left:23px;top:107px;font-size:8.5px;color:#2a8ba3}
.s4 .brand-name{left:55px;top:137px;width:190px;font-size:23px}
.s4 .brand-name small{font-size:13px;margin-top:3px}
.s4 .lorem{left:20px;width:265px;font-size:7px;text-align:center}
.s4 .lorem.a{top:194px}
.s4 .lorem.b{top:257px}
.s4 .figure-art{left:335px;top:140px;width:165px;height:185px;background:linear-gradient(135deg,#f4f4f4 0%,#e2e2e2 50%,#f2ee8a 100%)}
.s4 .contact-left{left:120px;width:230px;top:331px;font-size:9px;color:var(--grey);text-align:right}
.s4 .contact-left span{justify-content:flex-end}
.s4 .divider{left:355px;top:333px;width:1px;height:28px;background:#bbb}
.s4 .contact-right{left:362px;top:331px;font-size:9px;color:var(--grey)}
.s4 .contact-left i,.s4 .contact-right i{color:var(--brand)}
.s4 .band{left:175px;top:362px;width:343px;height:25px;background:var(--brand)}
.s4 .licence{left:182px;top:367px;font-size:9px;font-weight:700;color:var(--white);letter-spacing:.5px}
</style>
</head>
<body>
<main class="canvas">

  <p class="set-label" style="left:314px;top:130px">SET_1</p>
  <p class="set-label" style="left:871px;top:130px">SET_2</p>
  <p class="set-label" style="left:317px;top:685px">SET_ 3</p>
  <p class="set-label" style="left:868px;top:685px">SET_ 4</p>

  <section class="slide s1">
    <svg style="left:0;top:0" width="521" height="388" viewBox="0 0 521 388">
      <path d="M0 252 C150 220 280 300 380 270 C440 252 490 222 521 214 L521 388 L0 388Z" fill="#3fbdd8"/>
      <path d="M0 252 C150 220 280 300 380 270 C440 252 490 222 521 214" fill="none" stroke="#6d6e71" stroke-width="3"/>
    </svg>
    <div class="scene-art" role="img" aria-label="Business team silhouettes behind a wall clock and stacks of gold coins"></div>
    <h2 class="welcome">WELCOME</h2>
    <div class="brand-name"><span style="display:inline-block;width:12px;height:12px;border-radius:50%;background:var(--grey);margin-right:6px"></span>TELLMORA<small>FINANCIAL GROUP</small></div>
    <h3 class="headline">A PLAN TO PROTECT YOU</h3>
    <p class="tagline">Professional &amp; Individual advice to protect your greatest assets</p>
    <div class="contact">
      <span><i></i>1-234-567890</span>
      <span><i></i>www.tellmorafinancial.com</span>
      <span><i></i>john@tellmorafinancial.com</span>
      <span><i></i>Dummy city, Dummy Country Land</span>
    </div>
    <p class="licence">Authorised Representatives<br>of Corvallo AFS Licence No 508124</p>
  </section>

  <section class="slide s2">
    <div class="topband"></div>
    <div class="figure-art" role="img" aria-label="White 3D figure leaning on a yellow dollar sign"></div>
    <h2 class="headline">A PLAN TO PROTECT YOU</h2>
    <p class="tagline">Professional &amp; Individual advice to protect your greatest assets</p>
    <p class="lorem">Lorem Ipsum has been the industry's standard dummy text ever since the 1500s, when an unknown printer took a galley of type and scrambled it to make a type specimen book. It has survived not only five centuries, but also the leap into electronic typesetting, remaining essentially unchanged.</p>
    <p class="welcome">Welcome</p>
    <svg style="left:0;top:260px" width="360" height="70" viewBox="0 0 360 70">
      <rect x="150" y="6" width="210" height="14" fill="#8a8b8d"/>
      <polyline points="0,58 55,58 55,23 133,23" fill="none" stroke="#3fbdd8" stroke-width="1"/>
      <circle cx="133" cy="23" r="4" fill="#3fbdd8"/>
    </svg>
    <div class="brand-name">TELLMORA<small>FINANCIAL GROUP</small></div>
    <div class="contact">
      <span><i></i>1-234-567890</span>
      <span><i></i>www.tellmorafinancial.com</span>
      <span><i></i>john@tellmorafinancial.com</span>
      <span><i></i>Dummy city, Dummy Country Land</span>
    </div>
    <p class="licence">Authorised Representatives of Corvallo AFS Licence No 508124</p>
  </section>

  <section class="slide s3">
    <svg style="left:0;top:0" width="522" height="390" viewBox="0 0 522 390">
      <polyline points="0,378 100,262 140,282 262,165 300,205 468,92" fill="none" stroke="#a6dcea" stroke-width="40" stroke-linejoin="miter"/>
      <polyline points="0,368 100,252 140,272 262,155 300,195 460,82" fill="none" stroke="#1f7a8c" stroke-width="18" stroke-linejoin="miter"/>
      <polyline points="0,360 100,244 140,264 262,147 300,187 455,77" fill="none" stroke="#3fbdd8" stroke-width="16" stroke-linejoin="miter"/>
      <polygon points="395,80 488,52 470,145" fill="#3fbdd8"/>
    </svg>
    <h2 class="headline">A PLAN TO PROTECT YOU</h2>
    <p class="tagline">Professional &amp; Individual advice to protect your greatest assets</p>
    <p class="lorem a">Lorem Ipsum has been the industry's standard dummy text ever since the 1500s, when an unknown printer took a galley of type and scrambled it to make a type specimen book. It has survived not only five centuries, but also the leap into electronic typesetting, remaining essentially unchanged.</p>
    <p class="lorem b">Lorem Ipsum has been the industry's standard dummy text ever since the 1500s, when an unknown printer took a galley of type and scrambled it to make a type specimen book. It has survived not only five centuries, but also the leap into electronic typesetting, remaining</p>
    <div class="brand-name">TELLMORA<small>FINANCIAL GROUP</small></div>
    <div class="contact">
      <span>1-234-567890<i></i></span>
      <span>www.tellmorafinancial.com<i></i></span>
      <span>john@tellmorafinancial.com<i></i></span>
      <span>Dummy city, Dummy Country Land<i></i></span>
    </div>
    <div class="band"></div>
    <p class="licence">Authorised Representatives of Corvallo AFS Licence No 508124</p>
  </section>

  <section class="slide s4">
    <svg style="left:0;top:0" width="518" height="130" viewBox="0 0 518 130">
      <path d="M255 0 L518 0 L518 90 C430 60 330 30 255 0Z" fill="#3fbdd8"/>
      <path d="M270 20 C360 60 450 85 518 92" fill="none" stroke="#58595b" stroke-width="6"/>
      <path d="M280 38 C370 78 450 100 518 104" fill="none" stroke="#1f7a8c" stroke-width="4"/>
    </svg>
    <h2 class="headline">A PLAN TO<span>PROTECT YOU</span></h2>
    <p class="tagline">Professional &amp; Individual advice to protect your greatest assets</p>
    <div class="brand-name">TELLMORA<small>FINANCIAL GROUP</small></div>
    <p class="lorem a">Lorem Ipsum has been the industry's standard dummy text ever since the 1500s, when an unknown printer took a galley of type and scrambled it to make a type specimen book. It has survived not only five centuries, but also the leap into electronic typesetting, remaining essentially unchanged.</p>
    <p class="lorem b">Lorem Ipsum has been the industry's standard dummy text ever since the 1500s, when an unknown printer took a galley of type and scrambled it to make a type specimen book. It has survived not only five centuries, but also the leap into electronic typesetting, remaining essentially unchanged.</p>
    <div class="figure-art" role="img" aria-label="White 3D figure leaning on a yellow dollar sign"></div>
    <div class="contact contact-left">
      <span>www.tellmorafinancial.com<i></i></span>
      <span>Dummy city, Dummy Country Land<i></i></span>
    </div>
    <div class="divider"></div>
    <div class="contact contact-right">
      <span><i></i>1-234-567890</span>
      <span><i></i>john@tellmorafinancial.com</span>
    </div>
    <div class="band"></div>
    <p class="licence">Authorised Representatives of Corvallo AFS Licence No 508124</p>
  </section>

</main>
</body>
</html>
```